wardrobe/costume stylist needs good business card for own business

Hi:)

I'm wanting a business card for my company. I am a freelance stylist.

I do wardrobe/costume stylist to TV commercials; Films; Fashion and Lifestyle shoots.

I'd like a design based around my name Rosalind Parfrey written nicely, maybe a colour? Up to you?!

I've attached a couple of images of business cards I like
.... be creative and have fun!

Thank you :)

Reason: I was trying to get my new business card ready for before I headed overseas Friday morning but I don't think that was realistic so I'd like to extend the deadline to give time to the project. Thank you

Hi designers:) Thank you for all your designs, I've extended the deadline until Sunday, so there's a bit more time. I've attached 3 pictures of business cards which I quite like, please take a look to see if it can be of help in your process. I like the pale plain or patterned background with dark font and the dark plain or patterned background with the pale font the motifs the feminine fonts the plain fonts I like the idea of playing with a circle or some shape on one side of the card with my name or initials as in the picture I have on my post could you play around with this idea a bit please? Thank you all for the work you've done :) Rosa

Hi I am working overseas til Saturday night sorry for no feedback until I teturn Thanks :) Rosa

Hi designers, Thank you all so much for submitting your designs, I really appreciate your input into my project :) I'm sorry I didn't get to respond to some comments, and give feedback. I didn't back from being away until later than I expected, and the deadline had passed then, so apologies. Thanks to you all again for all your really good designs :) Rosa

Target Market(s)

I am a freelance stylist my target audience is producers, production companies, photographers, directors...

Industry/Entity Type

Business

Requirements
Must have
• Rosalind Parfrey
Stylist or Wardrobe Stylist

email rosaparfrey@mailbox-example.co.nz
Mobile 0218467193

(Don't have to use the words 'email' and 'mobile')
Nice to have
• Would like it to be double sided
Like B & W
Like pale colour background with dark font or white font
Like dark colour background with pale font
Should not have
• I would prefer it not to incorporate pictures

```html
<!DOCTYPE html>
<html lang="en">
<head>
<meta charset="utf-8">
<title>Rosalind Parfrey — Stylist Business Card</title>
<link rel="stylesheet" href="https://fonts.googleapis.com/css2?family=Great+Vibes&family=Encode+Sans+Condensed:wght@300&display=swap">
<style>
  :root {
    --page: #ffffff;
    --card: #e0d8b6;
    --ink: #6b6b6b;
    --light: #ffffff;
    --script: "Great Vibes", cursive;
    --sans: "Encode Sans Condensed", sans-serif;
  }
  html, body {
    margin: 0;
    padding: 0;
    width: 1000px;
    height: 1200px;
    overflow: hidden;
    background: var(--page);
  }
  .canvas {
    position: relative;
    width: 1000px;
    height: 1200px;
  }
  .card {
    position: absolute;
    left: 22px;
    width: 956px;
    height: 546px;
    background: var(--card);
  }
  .card--front { top: 43px; }
  .card--back  { top: 612px; }

  .card__name {
    position: absolute;
    left: 86px;
    top: 196px;
    margin: 0;
    font-family: var(--script);
    font-weight: 400;
    font-size: 84px;
    line-height: 1.2;
    color: var(--light);
    white-space: nowrap;
  }
  .card__role {
    position: absolute;
    left: 103px;
    top: 332px;
    margin: 0;
    font-family: var(--sans);
    font-weight: 300;
    font-size: 60px;
    line-height: 1.2;
    color: var(--ink);
  }
  .card__contact {
    position: absolute;
    right: 318px;
    top: 330px;
    margin: 0;
    text-align: right;
    font-family: var(--sans);
    font-weight: 300;
    font-size: 29px;
    line-height: 50px;
    color: var(--ink);
    font-style: normal;
  }
  .card__contact span { display: block; }

  .card__signature {
    position: absolute;
    left: 816px;
    top: 60px;
    height: 420px;
    margin: 0;
    writing-mode: vertical-rl;
    transform: rotate(180deg);
    font-family: var(--sans);
    font-weight: 300;
    font-size: 46px;
    line-height: 1;
    text-align: center;
    color: var(--ink);
    white-space: nowrap;
  }
</style>
</head>
<body>
  <main class="canvas">
    <section class="card card--front" aria-label="Card front">
      <h1 class="card__name">Rosalind Parfrey</h1>
      <p class="card__role">Stylist</p>
      <address class="card__contact">
        <span class="card__email">rosaparfrey@mailbox-example.co.nz</span>
        <span class="card__phone">0218467193</span>
      </address>
    </section>
    <section class="card card--back" aria-label="Card back">
      <p class="card__signature">Rosalind Parfrey</p>
    </section>
  </main>
</body>
</html>
```